Business card design needed

I would like a one sided black business card with the information provided above. Refer to my website www.brightvolleyracquets.com.au for an example of colors I have used for my site, would like to keep this consistent for my business cards also, I will upload my logo below.

I am a new small business that provides tennis customers with racquet re stringing, tennis strings and accessories.

Industry/Entity Type

Small Business

Contact Information for Business Card

Bright Volley Tennis

Owen Whitby
Managing Director

brightvolleyracquets@mailbox.example
www.brightvolleyracquets.com.au
0491 726 305

Racquet Restringing/Tennis Strings/Accessories

Requirements
Must have
• Must have my logo and card must be black

```html
<!DOCTYPE html>
<html lang="en">
<head>
<meta charset="utf-8">
<title>Bright Volley Tennis – Business Card</title>
<link href="https://fonts.googleapis.com/css2?family=Exo+2:ital,wght@0,400;0,800;1,400;1,500&display=swap" rel="stylesheet">
<style>
  :root {
    --backdrop: #e8e5e0;
    --card-black: #050505;
    --court-lime: #b9d538;
    --line-white: #ffffff;
    --strip-grey: #9ea39a;
    --ink-dark: #1b1d14;
    --text-white: #f2f2f2;
  }
  * { box-sizing: border-box; margin: 0; padding: 0; }
  html, body {
    width: 1200px; height: 475px; overflow: hidden;
    background: var(--backdrop);
    font-family: "Exo 2", Arial, sans-serif;
  }
  .canvas { position: relative; width: 1200px; height: 475px; }

  .card {
    position: absolute;
    width: 546px; height: 313px;
    border-radius: 14px;
    overflow: hidden;
    background: var(--card-black);
  }
  .card--front { left: 34px; top: 81px; }
  .card--back { left: 607px; top: 85px; }

  .card__court { position: absolute; inset: 0; }

  .brand {
    position: absolute;
    display: flex; align-items: center; gap: 12px;
    color: var(--court-lime);
    font-weight: 800;
    font-size: 30px;
    letter-spacing: 1px;
    text-transform: uppercase;
    white-space: nowrap;
  }
  .brand__dot {
    width: 34px; height: 34px; border-radius: 50%;
    background: var(--court-lime);
    flex: none;
  }
  .card--front .brand { left: 50%; top: 70px; transform: translateX(-50%); }
  .card--back .brand { left: 50%; top: 110px; transform: translateX(-50%); }

  .person {
    position: absolute; left: 44px; top: 232px;
    color: var(--ink-dark);
    font-style: italic;
  }
  .person__name { font-size: 20px; font-weight: 400; letter-spacing: 0.5px; text-transform: uppercase; line-height: 1.1; }
  .person__role { font-size: 13.5px; font-weight: 400; margin-top: 2px; }

  .contacts {
    position: absolute; left: 262px; top: 228px;
    list-style: none;
    color: var(--ink-dark);
    font-style: italic;
    font-size: 12.5px;
    line-height: 19px;
  }
  .contacts li { display: flex; align-items: center; gap: 8px; white-space: nowrap; }
  .contacts svg { width: 11px; height: 11px; flex: none; }
  .contacts .contacts__phone { padding-left: 17px; font-size: 14px; }
  .contacts .contacts__email { padding-left: 10px; }

  .back__url {
    position: absolute; left: 0; right: 0; top: 240px;
    text-align: center;
    color: var(--text-white);
    font-size: 13.5px;
    letter-spacing: 1.6px;
  }
</style>
</head>
<body>
<main class="canvas">

  <section class="card card--front" aria-label="Business card front">
    <svg class="card__court" viewBox="0 0 546 313" preserveAspectRatio="none" aria-hidden="true">
      <rect x="0" y="192" width="546" height="121" fill="var(--court-lime)"/>
      <rect x="0" y="190" width="546" height="5" fill="var(--strip-grey)"/>
      <line x1="285" y1="194" x2="216" y2="313" stroke="var(--line-white)" stroke-width="2"/>
      <line x1="285" y1="194" x2="546" y2="194" stroke="var(--line-white)" stroke-width="2"/>
    </svg>

    <div class="brand"><span class="brand__dot"></span>Bright Volley Tennis</div>

    <div class="person">
      <p class="person__name">Owen Whitby</p>
      <p class="person__role">Managing Director</p>
    </div>

    <ul class="contacts">
      <li class="contacts__phone">
        <svg viewBox="0 0 12 12" aria-hidden="true"><path d="M2.5 1 L4.5 1 L5.2 3.4 L4 4.3 Q5 6.8 7.7 8 L8.6 6.8 L11 7.5 L11 9.5 Q10.5 11 9 11 Q1 10 1 2.6 Q1 1 2.5 1 Z" fill="var(--ink-dark)"/></svg>
        0491 726 305
      </li>
      <li class="contacts__email">
        <svg viewBox="0 0 12 12" aria-hidden="true"><rect x="0.5" y="2.5" width="11" height="7.5" rx="1" fill="var(--ink-dark)"/><path d="M1 3 L6 7 L11 3" stroke="var(--court-lime)" stroke-width="1" fill="none"/></svg>
        brightvolleyracquets@mailbox.example
      </li>
      <li>
        <svg viewBox="0 0 12 12" aria-hidden="true"><circle cx="6" cy="6" r="5" fill="none" stroke="var(--ink-dark)" stroke-width="1.2"/><ellipse cx="6" cy="6" rx="2.2" ry="5" fill="none" stroke="var(--ink-dark)" stroke-width="1"/><line x1="1" y1="6" x2="11" y2="6" stroke="var(--ink-dark)" stroke-width="1"/></svg>
        www.brightvolleyracquets.com.au
      </li>
    </ul>
  </section>

  <section class="card card--back" aria-label="Business card back">
    <div class="brand"><span class="brand__dot"></span>Bright Volley Tennis</div>
    <p class="back__url">www.brightvolleyracquets.com.au</p>
  </section>

</main>
</body>
</html>
```